Pine leaf & Snapvista ad needed

I am in need of a simple static image ad to be used for Pineleaf & Snapvista. A photo of a nice roof on a nice house. "Instant Satellite Roof Estimates" "Your house, your time & instant estimate" . Our logo file is here: https://www.filecrate-example.net/share/q73kdm41xv9wpz2tbn8hs/JKsT4mWQpZ2xYcVn8bRfL6d?key=wm5tz81qvjx3c7bnd0ke9fa4r&v=0

Multiple variations will be purchased.

```html
<!DOCTYPE html>
<html lang="en">
<head>
<meta charset="utf-8">
<title>Crestline Roofing – Instant Satellite Roof Estimates</title>
<link rel="stylesheet" href="https://fonts.googleapis.com/css2?family=Lexend:wght@300;400;500;600&display=swap">
<style>
  :root {
    --ink: #000000;
    --paper: #ffffff;
    --frame-grey: #bdbdbd;
    --band-grey: #c2c2c2;
    --dot-blue: #a9d3ea;
    --sky: #cfd9e6;
    --roof: #8b918b;
    --roof-dark: #6d736f;
  }
  html, body {
    margin: 0;
    padding: 0;
    width: 1200px;
    height: 1200px;
    overflow: hidden;
    background: var(--ink);
  }
  .ad {
    position: relative;
    width: 1200px;
    height: 1200px;
    background: var(--ink);
    color: var(--paper);
    font-family: "Lexend", sans-serif;
    overflow: hidden;
  }
  .ad__shapes {
    position: absolute;
    inset: 0;
  }
  .brand {
    position: absolute;
    left: 56px;
    top: 96px;
    font-weight: 400;
    color: var(--paper);
    line-height: 1;
  }
  .brand__name {
    display: block;
    font-size: 66px;
    letter-spacing: 1px;
  }
  .brand__sub {
    display: block;
    font-size: 28px;
    letter-spacing: 5px;
    margin-top: 12px;
    padding-left: 196px;
  }
  .call {
    position: absolute;
    left: 833px;
    top: 78px;
    line-height: 1;
  }
  .call__label {
    font-size: 27px;
    font-weight: 500;
  }
  .call__number {
    font-size: 43px;
    font-weight: 500;
    letter-spacing: 1px;
    margin-top: 8px;
  }
  .headline {
    position: absolute;
    left: 33px;
    top: 340px;
    margin: 0;
    font-size: 70px;
    font-weight: 300;
    line-height: 95px;
    letter-spacing: 0.5px;
  }
  .tagline {
    position: absolute;
    left: 35px;
    top: 672px;
    margin: 0;
    font-size: 40px;
    font-weight: 300;
    line-height: 57px;
  }
  .cta {
    position: absolute;
    left: 41px;
    top: 898px;
    font-size: 38px;
    font-weight: 400;
    color: var(--ink);
    line-height: 1;
  }
  .license {
    position: absolute;
    left: 113px;
    top: 1098px;
    font-size: 25px;
    font-weight: 500;
    line-height: 30px;
    letter-spacing: 0.5px;
  }
</style>
</head>
<body>
<main class="ad">
  <svg class="ad__shapes" width="1200" height="1200" viewBox="0 0 1200 1200" aria-hidden="false">
    <defs>
      <linearGradient id="house-photo-tone" x1="0" y1="0" x2="0.2" y2="1">
        <stop offset="0" stop-color="var(--sky)"/>
        <stop offset="0.35" stop-color="#b9c3cf"/>
        <stop offset="0.55" stop-color="var(--roof)"/>
        <stop offset="1" stop-color="var(--roof-dark)"/>
      </linearGradient>
    </defs>

    <!-- dotted accent under the phone block -->
    <g class="dot-row" fill="var(--dot-blue)">
      <circle cx="654" cy="203" r="2.6"/><circle cx="670" cy="203" r="2.6"/><circle cx="686" cy="203" r="2.6"/><circle cx="702" cy="203" r="2.6"/><circle cx="718" cy="203" r="2.6"/><circle cx="734" cy="203" r="2.6"/><circle cx="750" cy="203" r="2.6"/><circle cx="766" cy="203" r="2.6"/><circle cx="782" cy="203" r="2.6"/><circle cx="798" cy="203" r="2.6"/>
      <circle cx="654" cy="215" r="2.6"/><circle cx="670" cy="215" r="2.6"/><circle cx="686" cy="215" r="2.6"/><circle cx="702" cy="215" r="2.6"/><circle cx="718" cy="215" r="2.6"/><circle cx="734" cy="215" r="2.6"/><circle cx="750" cy="215" r="2.6"/><circle cx="766" cy="215" r="2.6"/><circle cx="782" cy="215" r="2.6"/><circle cx="798" cy="215" r="2.6"/>
    </g>

    <!-- phone badge -->
    <circle class="call-badge" cx="751" cy="119" r="47" fill="var(--paper)"/>
    <g class="call-icon" fill="none" stroke="var(--ink)" stroke-width="2.6" stroke-linecap="round" stroke-linejoin="round">
      <path d="M737 105 q-4 4 -1 12 q6 14 20 21 q8 3 12 -1 l3 -4 q1 -2 -1 -4 l-7 -5 q-2 -1 -4 1 l-3 3 q-8 -4 -12 -12 l3 -3 q2 -2 1 -4 l-5 -7 q-2 -2 -4 -1 z"/>
      <path d="M756 104 q10 1 11 11"/>
      <path d="M756 96 q17 1 19 19"/>
    </g>

    <!-- photo frame and photo area -->
    <path class="photo-frame" d="M652 290 Q662 237 720 237 L1200 237 L1200 1200 L485 1200 Z" fill="var(--frame-grey)"/>
    <path class="house-photo" d="M672 310 Q680 264 732 264 L1200 264 L1200 1200 L505 1200 Z" fill="url(#house-photo-tone)" role="img" aria-label="Photo of a grey shingled house roof with a white-trimmed dormer against a pale blue sky"/>

    <!-- call-to-action band -->
    <path class="cta-band" d="M0 853 L612 853 Q630 853 626 870 L601 984 Q597 1000 580 1000 L0 1000 Z" fill="var(--band-grey)"/>

    <!-- license icon -->
    <g class="license-icon" fill="none" stroke="var(--paper)" stroke-width="2.4" stroke-linejoin="round" stroke-linecap="round">
      <path d="M48 1098 h38 v22"/>
      <path d="M48 1098 v52 h30"/>
      <path d="M56 1110 h22 M56 1119 h18 M56 1128 h14 M56 1137 h12"/>
      <circle cx="90" cy="1132" r="8"/>
      <path d="M85 1139 l-2 12 l7 -4 l7 4 l-2 -12"/>
    </g>
  </svg>

  <div class="brand">
    <span class="brand__name">CRESTLINE</span>
    <span class="brand__sub">ROOFING</span>
  </div>

  <div class="call">
    <div class="call__label">Call Us</div>
    <div class="call__number">123.456.7890</div>
  </div>

  <h1 class="headline">Instant Satellite<br>Roof<br>Estimates</h1>

  <p class="tagline">Your House, Your Time<br>and Instant Estimate</p>

  <div class="cta">Get Your FREE Estimates</div>

  <div class="license">Licensed &amp; Insured<br>No. 12345678</div>
</main>
</body>
</html>
```